Brindle Sky Port needs a new upscale business card design for our high end aircraft hangar complex

Brindle Sky Port (BSP) is a large, upscale jet hangar complex in the US housing expensive aircraft. We need a new business card design, using our current logo. We will be attending a industry convention and need a card design that will stand out and be remembered by aircraft owners and private pilots.

Target Market(s)

Aircraft pilots or owners looking for a new upscale hangar

Industry/Entity Type

Airport

Contact Information for Business Card

I like to use very heavy card stock, 400#, double sided. Square, no rounded edges please.

Colors
3276b5
0255a3
85abd2

Requirements
Must have
• An expensive, classy design, vivid colors.
Nice to have
• Needs to look very expensive and classy, and have some "pop". Designer must be able to download or copy my current typeface or fonts.
• One card side might be black with the "Logo and Brindle Sky Port Double line image in blue (or try gold, or glossy black), and perhaps have a grayed out "K720 jet silhouette". The other card side would have our contact info, and perhaps the "BSP Logo only". I'd like my contact info 'stacked', not in a paragraph format.
Should not have
• Should not look "too busy". Having a double-sided card will help.

```html
<!DOCTYPE html>
<html lang="en">
<head>
<meta charset="utf-8">
<title>Brindle Sky Port — Business Card</title>
<link href="https://fonts.googleapis.com/css2?family=Open+Sans:wght@400;600;700&display=swap" rel="stylesheet">
<style>
  :root {
    --backdrop: #8e8e8e;
    --card-black: #0a0a0b;
    --brand-blue: #3276b5;
    --brand-deep: #0255a3;
    --brand-light: #85abd2;
    --ink-white: #f2f2f2;
    --rule-grey: #8a8a8a;
    --silhouette: #1c1c1e;
  }
  * { box-sizing: border-box; margin: 0; padding: 0; }
  html, body {
    width: 1200px; height: 844px; overflow: hidden;
    background: var(--backdrop);
    font-family: "Open Sans", Arial, sans-serif;
  }
  .sheet {
    width: 1200px; height: 844px;
    display: flex; align-items: center; justify-content: center; gap: 60px;
  }
  .card {
    position: relative;
    width: 525px; height: 300px;
    background: var(--card-black);
    overflow: hidden;
    box-shadow: 0 14px 30px rgba(0,0,0,.35);
  }

  /* Contact side */
  .card-contact .wordmark {
    position: absolute; top: 44px; right: 74px;
    color: var(--brand-blue); font-weight: 700; font-size: 54px; letter-spacing: 2px;
    line-height: 1;
  }
  .contact-person { position: absolute; top: 60px; left: 40px; }
  .person-name {
    color: var(--brand-blue); font-weight: 600; font-size: 15px; letter-spacing: 1px;
    text-transform: uppercase;
  }
  .person-title { color: var(--ink-white); font-size: 11px; margin-top: 2px; }
  .contact-lines { list-style: none; margin-top: 12px; }
  .contact-lines li {
    display: flex; align-items: center; gap: 8px;
    color: var(--ink-white); font-size: 12px; line-height: 17px;
  }
  .contact-lines svg { width: 11px; height: 11px; fill: var(--brand-light); flex: none; }
  .contact-lines .email { margin-left: 19px; }
  .contact-rule {
    position: absolute; top: 192px; left: 40px; right: 40px;
    height: 1px; background: var(--rule-grey);
  }
  .contact-address {
    position: absolute; top: 206px; right: 40px;
    text-align: right; font-style: normal;
    color: var(--ink-white); font-size: 13px; line-height: 19px;
  }

  /* Brand side */
  .jet-silhouette {
    position: absolute; left: 0; top: 0; width: 300px; height: 300px;
  }
  .brand-lockup {
    position: absolute; top: 96px; right: 44px;
    text-align: center; color: var(--brand-blue); font-weight: 700;
  }
  .brand-lockup .initials { font-size: 64px; line-height: 1; letter-spacing: 3px; }
  .brand-lockup .full-name {
    font-size: 19px; letter-spacing: 2px; text-transform: uppercase; margin-top: 6px;
  }
</style>
</head>
<body>
<main class="sheet">

  <section class="card card-contact" aria-label="Card back, contact details">
    <div class="wordmark">BSP</div>
    <div class="contact-person">
      <p class="person-name">Alden Marsh</p>
      <p class="person-title">CEO / Founder</p>
      <ul class="contact-lines">
        <li><svg viewBox="0 0 12 12"><path d="M2.5 0.5l2 2.2-1.1 1.4c.7 1.6 2 2.9 3.6 3.6l1.4-1.1 2.2 2-1.2 2.2C5 10.6 1.4 7 .4 1.7z"/></svg>555 214 7730</li>
        <li><svg viewBox="0 0 12 12"><path d="M3 0h6v12H3zM4 1.5v8h4v-8zM5.4 10.3h1.2v.9H5.4z" fill-rule="evenodd"/></svg>555 381 6042</li>
        <li><svg viewBox="0 0 12 12"><path d="M3 0h6v3h2v7H1V3h2zM4 1v3h4V1zM3 6h6v1H3zM3 8h6v1H3z" fill-rule="evenodd"/></svg>555 907 2158</li>
        <li class="email">alden@BrindleSkyPort.com</li>
      </ul>
    </div>
    <div class="contact-rule"></div>
    <address class="contact-address">
      2190 Larkspur Way<br>
      Juneau, Alaska 34581<br>
      BrindleSkyPort.com
    </address>
  </section>

  <section class="card card-brand" aria-label="Card front, brand side">
    <svg class="jet-silhouette" role="img" aria-label="Faint grey silhouette of a K720 business jet seen from the front" viewBox="0 0 300 300">
      <defs>
        <radialGradient id="jetTone" cx="45%" cy="55%" r="55%">
          <stop offset="0" stop-color="#1e1e20"/>
          <stop offset="1" stop-color="#0a0a0b"/>
        </radialGradient>
      </defs>
      <rect width="300" height="300" fill="url(#jetTone)"/>
    </svg>
    <div class="brand-lockup">
      <div class="initials">BSP</div>
      <div class="full-name">Brindle Sky Port</div>
    </div>
  </section>

</main>
</body>
</html>
```